Commercial Refrigeration Service Company requires stylish and fresh looking flyer.

We need a flyer to hand out to new customers. It should have a photo and our branding, list all the services that are offered and our contact details.
We would like two flyers to be supplied, both identical though one offering a discount until July ( Half Price Service Fee ). The flyer should be clear, interesting and in similar colours to the branding package supplied.
Please look at our website for information about the services on offer:
www.brisko-coolworks.com.au

Target Market(s)

Cafes, bars, restaurants, pubs ect.

Font styles to use
Other font styles liked:
• Font package provided

Colors
85cae6
ffffff
333333

Requirements
Must have
• - The photo provided.
• - The company logo.
• - Similar feel to the website & business card.
• - Smooth layout and clear to understand.
Should not have
• - No clunky badges or prints.

```html
<!DOCTYPE html>
<html lang="en">
<head>
<meta charset="utf-8">
<title>Brisko Commercial Refrigeration – Flyer</title>
<link rel="stylesheet" href="https://fonts.googleapis.com/css2?family=Didact+Gothic&family=Montserrat:wght@700&display=swap">
<style>
  :root {
    --brand-blue: #5bc3ea;
    --accent-blue: #56bbe3;
    --text-blue: #4fb8e2;
    --ink: #2e2e2e;
    --dark-panel: #2f2f2f;
    --paper: #f1f1f1;
    --paper-edge: #e6e6e6;
    --white: #ffffff;
    --backdrop: #707070;
  }
  * { margin: 0; padding: 0; box-sizing: border-box; }
  html, body {
    width: 1200px; height: 1146px; overflow: hidden;
    background: var(--backdrop);
  }
  .flyer {
    position: absolute; left: 305px; top: 113px;
    width: 636px; height: 900px;
    background: var(--paper);
    overflow: hidden;
  }
  .hero-photo {
    position: absolute; left: 0; top: 0; width: 636px; height: 302px;
    background: linear-gradient(180deg, #8fb7d8 0%, #b9cfdf 22%, #9aa6ad 40%, #6f7478 62%, #55595c 100%);
  }
  .brand-band {
    position: absolute; left: 0; top: 302px; width: 636px; height: 126px;
    background: var(--brand-blue);
    display: flex; align-items: center; justify-content: center;
  }
  .brand-name {
    font-family: "Montserrat", sans-serif; font-weight: 700;
    font-size: 44px; letter-spacing: 0;
    color: var(--ink);
  }
  .offer-panel {
    position: absolute; left: 0; top: 428px; width: 636px; height: 205px;
    background: linear-gradient(180deg, var(--paper) 0%, var(--paper-edge) 100%);
  }
  .tagline {
    position: absolute; top: 22px; width: 100%;
    text-align: center;
    font-family: "Didact Gothic", sans-serif; font-size: 20px;
    letter-spacing: 0; color: var(--ink);
  }
  .discount-box {
    position: absolute; left: 90px; top: 78px; width: 456px; height: 85px;
    border: 1px solid var(--text-blue);
    text-align: center; color: var(--text-blue);
    font-family: "Didact Gothic", sans-serif;
  }
  .discount-title { font-size: 33px; line-height: 1; margin-top: 13px; letter-spacing: -0.5px; }
  .discount-note { font-size: 19px; line-height: 1; margin-top: 6px; letter-spacing: -0.3px; white-space: nowrap; }
  .services-panel {
    position: absolute; left: 0; top: 633px; width: 636px; height: 267px;
    background: var(--dark-panel);
  }
  .services-panel svg.shapes { position: absolute; left: 0; top: 0; }
  .service-list {
    position: absolute; left: 41px; top: 14px; list-style: none;
  }
  .service-list li {
    font-family: "Montserrat", sans-serif; font-weight: 700;
    font-size: 20px; line-height: 31.5px; color: var(--white);
    display: flex; align-items: center; gap: 7px;
  }
  .service-list li::before {
    content: ""; width: 8px; height: 8px;
    border: 2px solid var(--accent-blue);
    transform: rotate(45deg); margin-right: 1px;
  }
  .contact {
    position: absolute; right: 40px; top: 191px;
    text-align: right; color: var(--white);
    font-style: normal;
    font-family: "Didact Gothic", sans-serif; font-size: 18.5px; line-height: 20.5px;
  }
</style>
</head>
<body>
  <main class="flyer">
    <div class="hero-photo" role="img" aria-label="Photo of a technician leaning against the company ute parked by the beach"></div>

    <header class="brand-band">
      <span class="brand-name">Brisko</span>
    </header>

    <section class="offer-panel">
      <p class="tagline">Commercial Refrigeration</p>
      <div class="discount-box">
        <p class="discount-title">DISCOUNT UNTIL JULY</p>
        <p class="discount-note">PAY ONLY HALF PRICE OF THE SERVICE FEE</p>
      </div>
    </section>

    <section class="services-panel">
      <svg class="shapes" width="636" height="267" viewBox="0 0 636 267" aria-hidden="true">
        <polygon points="333,178 636,178 636,267 0,267 0,250 282,250" fill="var(--accent-blue)"/>
      </svg>
      <ul class="service-list">
        <li>Commercial Refrigeration</li>
        <li>Ice Makers</li>
        <li>Beer Systems</li>
        <li>Electrical</li>
        <li>24hr Service</li>
        <li>Sales</li>
        <li>Installation</li>
      </ul>
      <address class="contact">
        0412 555 018<br>
        Info@brisko-coolworks.com.au<br>
        www.brisko-coolworks.com.au
      </address>
    </section>
  </main>
</body>
</html>
```